Veltrane Group Business Card Design

The CEO is looking for a new trendy look for his business card.
You can stay with current branding or come up with something new/creative. It can be 3D, including Medical Office buildings. You can use our logo in a variety of colors. Please include name, title, company name, company website, email address, cell number

Target Market(s)

Real Estate Development and Construction

Industry/Entity Type

Health care real estate

Contact Information for Business Card

Rohesh Kamdar, CEO M-604.781.2249 E-roheshkamdar@veltrane.com Address:4180 Lindqvist Ave, Tampa, FL 33482 www.veltrane.com

Font styles to use
Other font styles liked:
• Be creative

Requirements
Must have
• Creative, trendy look
Nice to have
• Please go to our website to get a feel- www. veltrane.com
Should not have
• small fonts

```html
<!DOCTYPE html>
<html lang="en">
<head>
<meta charset="utf-8">
<title>Veltrane Group – Business Card</title>
<link rel="stylesheet" href="https://fonts.googleapis.com/css2?family=Montserrat:wght@300;400;700;800&display=swap">
<style>
  :root {
    --backdrop: #2a2a2a;
    --card: #141414;
    --ink: #ffffff;
    --ink-soft: #e6e6e6;
  }
  * { margin: 0; padding: 0; box-sizing: border-box; }
  html, body {
    width: 1200px; height: 1015px; overflow: hidden;
    background: var(--backdrop);
    font-family: "Montserrat", sans-serif;
  }
  .canvas {
    width: 1200px; height: 1015px;
    display: flex; flex-direction: column; align-items: center; justify-content: center;
    gap: 60px;
  }
  .card {
    position: relative;
    width: 700px; height: 400px;
    background: var(--card);
    color: var(--ink);
    box-shadow: 0 12px 30px rgba(0,0,0,.45);
  }
  .wordmark {
    position: absolute;
    font-weight: 800;
    line-height: .9;
    color: var(--ink);
    text-align: right;
    letter-spacing: -2px;
    white-space: nowrap;
  }
  .wordmark .sub { display: block; font-size: .42em; letter-spacing: 0; }
  .card--front .wordmark { font-size: 118px; right: 90px; top: 120px; }
  .card--back .wordmark { font-size: 74px; right: 40px; top: 48px; }
  .holder { position: absolute; left: 60px; top: 96px; }
  .holder__name { font-weight: 700; font-size: 24px; letter-spacing: .5px; white-space: nowrap; }
  .holder__title { font-weight: 300; font-size: 16px; margin-top: 4px; color: var(--ink-soft); }
  .contact { position: absolute; left: 60px; bottom: 42px; font-weight: 300; font-size: 17px; color: var(--ink-soft); }
  .contact__address { line-height: 1.3; margin-bottom: 22px; }
  .contact__list { list-style: none; }
  .contact__list li { display: flex; align-items: center; gap: 12px; line-height: 1.7; }
  .contact__list svg { width: 16px; height: 16px; fill: var(--ink); flex: none; }
</style>
</head>
<body>
<main class="canvas">
  <section class="card card--front">
    <div class="wordmark">Veltrane<span class="sub">group</span></div>
  </section>

  <section class="card card--back">
    <div class="holder">
      <div class="holder__name">Rohesh Kamdar</div>
      <div class="holder__title">CEO</div>
    </div>
    <div class="wordmark">Veltrane<span class="sub">group</span></div>
    <div class="contact">
      <p class="contact__address">4180 Lindqvist Ave,<br>Tampa, FL 33482</p>
      <ul class="contact__list">
        <li>
          <svg viewBox="0 0 16 16" aria-hidden="true"><path d="M3.5 1.5l2.5 0 1 3.5-1.6 1.2a8 8 0 0 0 4.4 4.4L11 9l3.5 1v2.5c0 1-1 2-2 2C6.5 14.5 1.5 9.5 1.5 3.5c0-1 1-2 2-2z"/></svg>
          604.781.2249
        </li>
        <li>
          <svg viewBox="0 0 16 16" aria-hidden="true"><path d="M1 3h14v10H1z M1.5 3.5L8 9l6.5-5.5" stroke="#141414" stroke-width="1.2"/></svg>
          roheshkamdar@veltrane.com
        </li>
        <li>
          <svg viewBox="0 0 16 16" aria-hidden="true"><circle cx="8" cy="8" r="7"/><path d="M1 8h14M8 1c3 3 3 11 0 14M8 1c-3 3-3 11 0 14" stroke="#141414" stroke-width="1" fill="none"/></svg>
          www.veltrane.com
        </li>
      </ul>
    </div>
  </section>
</main>
</body>
</html>
```